Local Roofing/Construction company business needs new biz card design

We need a new business card design, current cards are from the start of this operation and generic at best. We are a local Construction Company (General Contractor) with a majority of our work originating from insurance claims-exterior finish work is the main focus (Roofs-Siding-Gutters etc). Heavily involved with homeowners and the low ball offers they receive from insurance company's after a insurable event takes place. I have attached some of our original logo file(s) below.

```html
<!DOCTYPE html>
<html lang="en">
<head>
<meta charset="utf-8">
<title>Ridgeline Builders – Business Card</title>
<link rel="stylesheet" href="https://fonts.googleapis.com/css2?family=Montserrat:wght@400;500;600;700&display=swap">
<style>
  :root {
    --stage: #e9e7e4;
    --card-light: #243132;
    --card-dark: #0b1516;
    --green: #3fa45a;
    --green-bright: #2fb24a;
    --text-soft: #d7dddc;
    --pattern-a: #1c2a2b;
    --pattern-b: #0f1a1b;
  }
  * { box-sizing: border-box; margin: 0; padding: 0; }
  html, body { width: 1200px; height: 716px; overflow: hidden; }
  body {
    background: var(--stage);
    font-family: "Montserrat", sans-serif;
    position: relative;
  }
  .card {
    position: absolute;
    top: 203px;
    width: 540px;
    height: 309px;
    overflow: hidden;
    box-shadow: 0 10px 24px rgba(0,0,0,.25);
  }
  .card--back {
    left: 40px;
    border-bottom: 5px solid var(--green-bright);
  }
  .card--front {
    left: 620px;
    background: linear-gradient(160deg, var(--card-light) 0%, var(--card-dark) 70%);
    color: var(--text-soft);
  }

  /* back side */
  .back-pattern {
    position: absolute; inset: 0;
    background: radial-gradient(ellipse at 70% 45%, var(--pattern-a), var(--pattern-b) 75%);
  }
  .back-mark {
    position: absolute;
    left: 300px; top: 205px;
    display: flex; align-items: center; gap: 6px;
    font-weight: 700; font-size: 11px; letter-spacing: .5px;
    color: var(--green);
    text-transform: uppercase;
  }
  .back-mark__square { width: 10px; height: 10px; background: var(--green); }

  /* front side */
  .brand {
    position: absolute;
    right: 30px; top: 46px;
    display: flex; align-items: center; gap: 10px;
    font-weight: 700; font-size: 22px; letter-spacing: .5px;
    color: var(--green);
    text-transform: uppercase;
  }
  .brand__square { width: 22px; height: 22px; background: var(--green); }

  .identity { position: absolute; left: 30px; top: 96px; padding-left: 18px; }
  .identity__bar {
    position: absolute; left: 0; top: 2px;
    width: 9px; height: 30px; background: var(--green);
  }
  .identity__name {
    font-weight: 600; font-size: 19px; letter-spacing: .8px;
    color: var(--green); text-transform: uppercase; line-height: 1.1;
  }
  .identity__title { font-size: 11px; margin-top: 3px; }

  .divider {
    position: absolute; left: 150px; right: 60px; top: 152px;
    height: 1px; background: var(--green-bright);
  }

  .contact { position: absolute; left: 36px; top: 168px; list-style: none; }
  .contact__item {
    display: flex; align-items: center; gap: 8px;
    font-size: 12px; line-height: 21px;
  }
  .contact__icon { width: 10px; height: 10px; fill: var(--green); flex: none; }

  .address {
    position: absolute; right: 40px; bottom: 40px;
    text-align: right; font-size: 13px; line-height: 19px;
  }
</style>
</head>
<body>

<section class="card card--back" aria-label="Card back">
  <div class="back-pattern" role="img" aria-label="Faint repeated company emblem pattern on dark green-black background"></div>
  <div class="back-mark"><span class="back-mark__square"></span>Ridgeline Builders</div>
</section>

<section class="card card--front" aria-label="Card front">
  <div class="brand"><span class="brand__square"></span>Ridgeline Builders</div>

  <div class="identity">
    <span class="identity__bar"></span>
    <h1 class="identity__name">Daniel Morrow</h1>
    <p class="identity__title">Managing Director</p>
  </div>

  <div class="divider"></div>

  <ul class="contact">
    <li class="contact__item">
      <svg class="contact__icon" viewBox="0 0 10 10"><path d="M2 0.5 L3.6 2.6 L2.8 3.6 Q4 6 6.4 7.2 L7.4 6.4 L9.5 8 L8.4 9.5 Q1 8 0.5 1.6 Z"/></svg>
      0400 127 563
    </li>
    <li class="contact__item">
      <svg class="contact__icon" viewBox="0 0 10 10"><path d="M0.5 2 H9.5 V8.5 H0.5 Z M0.5 2 L5 5.5 L9.5 2" stroke="#0b1516" stroke-width=".8"/></svg>
      info@ridgelinebuilders.com
    </li>
    <li class="contact__item">
      <svg class="contact__icon" viewBox="0 0 10 10"><circle cx="5" cy="5" r="4.5"/><path d="M0.5 5 H9.5 M5 0.5 Q2.5 5 5 9.5 Q7.5 5 5 0.5" stroke="#0b1516" stroke-width=".7" fill="none"/></svg>
      www.ridgelinebuilders.com
    </li>
  </ul>

  <address class="address" style="font-style:normal">
    418 Harbor Avenue<br>
    Westfield County 5120
  </address>
</section>

</body>
</html>
```